Business Card for Dental Office - "online review card"

I would like to develop a tasteful card (that would compliment my existing business card) that provides my patients a written link to a portal on my website that would facilitate the generation of online reviews.

My existing business card was a Lumaquarry project a few years ago and has been well received. I hope that it is easily accessed online for reference.

Target Market(s)

Existing patients who need guidance in accessing the "write a review" section of my website

Industry/Entity Type

Business

Requirements
Must have
• -a similar look to my existing card:
http://www.lumaquarry.com.au/contest.aspx?id=5192&page=3

-a link to the following url in writing:
http://www.tessaroldental.com/reviews.html

- a reference to "appreciating feedback" or "how are we doing?"

```html
<!DOCTYPE html>
<html lang="en">
<head>
<meta charset="utf-8">
<title>Elena M. Tessaro, DDS – Review Card</title>
<link rel="stylesheet" href="https://fonts.googleapis.com/css2?family=Questrial&family=Open+Sans:wght@400;700&display=swap">
<style>
  :root {
    --backdrop: #dcdcdc;
    --card: #ffffff;
    --card-edge: #8a8a8a;
    --brand-blue: #35358f;
    --brand-blue-deep: #27277a;
    --brand-blue-light: #4a4aa8;
    --name-grey: #5e5e5e;
    --on-blue: #ffffff;
  }
  * { box-sizing: border-box; margin: 0; padding: 0; }
  html, body {
    width: 1200px; height: 711px; overflow: hidden;
    background: var(--backdrop);
  }
  .canvas { position: relative; width: 1200px; height: 711px; }

  .card {
    position: absolute;
    width: 514px; height: 292px;
    background: var(--card);
    border: 1px solid var(--card-edge);
    border-radius: 8px;
    overflow: hidden;
  }
  .card--review { left: 54px; top: 39px; border: none; }
  .card--front  { left: 627px; top: 39px; }
  .card--back   { left: 346px; top: 369px; }

  .brand-square {
    position: absolute;
    background: var(--brand-blue);
    border-radius: 6px;
  }
  .brand-name {
    position: absolute;
    font-family: "Questrial", sans-serif;
    font-weight: 400;
    color: var(--name-grey);
    white-space: nowrap;
    line-height: 1;
  }
  .brand-name .credential { font-size: 0.72em; }
  .brand-tagline {
    position: absolute;
    font-family: "Questrial", sans-serif;
    font-weight: 400;
    color: var(--name-grey);
    text-transform: uppercase;
    white-space: nowrap;
    line-height: 1;
  }

  /* review card */
  .wave-band { position: absolute; left: 0; top: 0; width: 514px; height: 292px; }
  .card--review .brand-square { left: 52px; top: 56px; width: 80px; height: 80px; }
  .card--review .brand-name { left: 158px; top: 64px; font-size: 25px; }
  .card--review .brand-tagline { right: 54px; top: 92px; font-size: 10px; letter-spacing: 2.4px; }
  .review-invite {
    position: absolute; left: 0; right: 0; top: 212px;
    text-align: center;
    font-family: "Open Sans", sans-serif;
    font-weight: 400; font-size: 17px;
    color: var(--on-blue);
    text-transform: uppercase;
  }
  .review-link {
    position: absolute; left: 0; right: 0; top: 246px;
    text-align: center;
    font-family: "Open Sans", sans-serif;
    font-weight: 700; font-size: 17px;
    color: var(--on-blue);
  }

  /* front card */
  .card--front .brand-square { left: 38px; top: 97px; width: 90px; height: 90px; }
  .card--front .brand-name { left: 156px; top: 104px; font-size: 31px; }
  .card--front .brand-tagline { right: 32px; top: 139px; font-size: 11.5px; letter-spacing: 2.8px; }

  /* back card */
  .card--back .brand-square { left: 171px; top: 38px; width: 176px; height: 176px; border-radius: 14px; }
  .card--back .brand-name { left: 0; right: 0; top: 226px; text-align: center; font-size: 18px; }
  .card--back .brand-tagline { left: 0; right: 0; top: 249px; text-align: center; font-size: 6.5px; letter-spacing: 1.6px; }
</style>
</head>
<body>
<main class="canvas">

  <section class="card card--review" aria-label="Review card">
    <svg class="wave-band" viewBox="0 0 514 292" aria-hidden="true">
      <defs>
        <linearGradient id="bandFill" x1="0" y1="0" x2="1" y2="1">
          <stop offset="0" stop-color="var(--brand-blue-light)"/>
          <stop offset="0.5" stop-color="var(--brand-blue)"/>
          <stop offset="1" stop-color="var(--brand-blue-deep)"/>
        </linearGradient>
      </defs>
      <path fill="url(#bandFill)" d="M0,132 H36 V140 Q36,154 50,154 H136 Q150,154 150,140 V128 C230,104 330,116 420,140 C462,151 494,128 514,108 V292 H0 Z"/>
      <path fill="none" stroke="#ffffff" stroke-width="3" d="M150,138 C240,116 340,128 428,152 C468,162 498,140 514,124"/>
      <path fill="none" stroke="#ffffff" stroke-width="1.5" d="M290,130 C340,138 390,152 432,162 C470,170 498,150 514,136"/>
      <path fill="none" stroke="#ffffff" stroke-width="2" d="M0,140 C12,138 24,136 36,136"/>
    </svg>
    <div class="brand-square"></div>
    <p class="brand-name">Elena M. Tessaro, <span class="credential">DDS</span></p>
    <p class="brand-tagline">and associates</p>
    <p class="review-invite">Appreciating feedback</p>
    <p class="review-link">http://www.tessaroldental.com/reviews.html</p>
  </section>

  <section class="card card--front" aria-label="Business card front">
    <div class="brand-square"></div>
    <p class="brand-name">Elena M. Tessaro, <span class="credential">DDS</span></p>
    <p class="brand-tagline">and associates</p>
  </section>

  <section class="card card--back" aria-label="Business card back">
    <div class="brand-square"></div>
    <p class="brand-name">Elena M. Tessaro, <span class="credential">DDS</span></p>
    <p class="brand-tagline">Family and cosmetic dentistry</p>
  </section>

</main>
</body>
</html>
```